Solar Company Bussiness Card

I need a 2 sided business card and would like a .psd and any font files for each side of the card. I would like my logo used, it should be attached with the fonts. I'm not opposed to the font colors with the logo being changed.

On the sample design, I'd like the following:

Marcus Dellow
President
Phone: 555-382-9174
www.brightvanepower.example

As I've recently opened in a 2nd market, I'm not sure about an address as I currently have 2 of them. I may actually get separate cards printed, one batch for each address, that's why I need the PSD file.
Updates

I'm very pleased with the response and designs I've received here for my business card. First and foremost, I'd like to thank everyone who took the time to submit a design. There truly are a lot of great designs in the bunch here and I'm having a little difficulty deciding. I will be reaching out to someone in the next day or two here to go to a final design. At this time, I'm not looking for any new concepts. If any of you do logos, I'm looking for a new logo for our sister entity, Dellow Partners, Inc. Thanks, Marcus Dellow

Reason: I'm not looking for any new designs at this point, but extending this deadline in order to give people I've asked a chance to re-submit items.

Industry/Entity Type

Business

```html
<!DOCTYPE html>
<html lang="en">
<head>
<meta charset="utf-8">
<title>Brightvane Power – Business Card</title>
<link rel="stylesheet" href="https://fonts.googleapis.com/css2?family=Exo+2:wght@400;500;600&display=swap">
<style>
  :root {
    --canvas-bg: #6a6a6a;
    --card-white: #ffffff;
    --card-shade: #eceef0;
    --brand-navy: #1f4f8f;
    --brand-blue: #1d66c8;
    --name-ink: #3b3f9a;
    --body-ink: #333333;
    --contact-ink: #ffffff;
  }
  * { box-sizing: border-box; margin: 0; padding: 0; }
  html, body { width: 1200px; height: 750px; overflow: hidden; }
  body {
    background: var(--canvas-bg);
    font-family: "Exo 2", "Segoe UI", sans-serif;
    position: relative;
  }
  .card {
    position: absolute;
    top: 220px;
    width: 540px;
    height: 309px;
    background: linear-gradient(160deg, var(--card-white) 40%, var(--card-shade));
    overflow: hidden;
  }
  .card--front { left: 40px; }
  .card--back { left: 620px; }

  .wordmark {
    display: flex;
    align-items: center;
    gap: 12px;
    color: var(--brand-navy);
    font-weight: 500;
    letter-spacing: 0.5px;
  }
  .wordmark__square {
    width: 40px;
    height: 40px;
    background: var(--brand-blue);
    flex: none;
  }
  .wordmark__text {
    display: flex;
    flex-direction: column;
    align-items: flex-end;
    line-height: 1;
  }
  .card--front .wordmark {
    position: absolute;
    left: 0; right: 0; top: 112px;
    justify-content: center;
    font-size: 40px;
  }

  .card__art { position: absolute; inset: 0; }

  .card--back .wordmark {
    position: absolute;
    left: 28px; top: 108px;
    font-size: 28px;
    gap: 10px;
  }
  .card--back .wordmark__square { width: 30px; height: 30px; }

  .holder {
    position: absolute;
    left: 34px; top: 190px;
  }
  .holder__name {
    color: var(--name-ink);
    font-size: 15px;
    font-weight: 600;
    letter-spacing: 1.2px;
    text-transform: uppercase;
  }
  .holder__role {
    color: var(--body-ink);
    font-size: 12.5px;
    margin-top: 2px;
  }

  .contact {
    position: absolute;
    right: 22px; top: 30px;
    color: var(--contact-ink);
    font-size: 12.5px;
    text-align: right;
    line-height: 1.45;
    list-style: none;
  }
  .contact__address { margin-bottom: 10px; }
  .contact li { display: flex; justify-content: flex-end; align-items: center; gap: 7px; }
  .contact svg { width: 12px; height: 12px; flex: none; }
</style>
</head>
<body>

<section class="card card--front" aria-label="Card front">
  <div class="wordmark">
    <span class="wordmark__square"></span>
    <span class="wordmark__text"><span>Brightvane</span><span>Power</span></span>
  </div>
</section>

<section class="card card--back" aria-label="Card back">
  <svg class="card__art" viewBox="0 0 540 309" aria-hidden="true">
    <defs>
      <radialGradient id="blueGlow" cx="0.62" cy="0.55" r="0.7">
        <stop offset="0" stop-color="#12a8e8"/>
        <stop offset="1" stop-color="#1d55c2"/>
      </radialGradient>
      <linearGradient id="greyBand" x1="0" y1="0" x2="1" y2="0">
        <stop offset="0" stop-color="#d7d8da"/>
        <stop offset="1" stop-color="#8e9093"/>
      </linearGradient>
    </defs>
    <path d="M300,0 Q205,140 188,309 L214,309 Q228,140 330,0 Z" fill="url(#greyBand)"/>
    <path d="M318,0 Q222,140 206,309" fill="none" stroke="#5c5e61" stroke-width="4"/>
    <path d="M335,0 Q236,140 222,309 L540,309 L540,0 Z" fill="url(#blueGlow)"/>
  </svg>

  <div class="wordmark">
    <span class="wordmark__square"></span>
    <span class="wordmark__text"><span>Brightvane</span><span>Power</span></span>
  </div>

  <div class="holder">
    <p class="holder__name">Marcus Dellow</p>
    <p class="holder__role">Managing Director</p>
  </div>

  <ul class="contact">
    <li class="contact__address">214 Harbor Street, Suite 6<br>Northfield, ST 10482</li>
    <li>555-382-9174
      <svg viewBox="0 0 12 12"><path d="M2 1 L4.5 1 L5.2 3.6 L3.8 4.6 Q5 7 7.4 8.2 L8.4 6.8 L11 7.5 L11 10 Q5 11 1 3 Z" fill="#fff"/></svg>
    </li>
    <li>555-382-9174
      <svg viewBox="0 0 12 12"><rect x="3" y="0.5" width="6" height="11" rx="1" fill="none" stroke="#fff"/><circle cx="6" cy="9.5" r="0.8" fill="#fff"/></svg>
    </li>
    <li>555-382-9175
      <svg viewBox="0 0 12 12"><rect x="1" y="5" width="10" height="6" fill="#fff"/><rect x="3" y="1" width="6" height="4" fill="none" stroke="#fff"/></svg>
    </li>
    <li>info@brightvanepower.example
      <svg viewBox="0 0 12 12"><rect x="0.5" y="2.5" width="11" height="7" fill="none" stroke="#fff"/><path d="M0.5 2.5 L6 7 L11.5 2.5" fill="none" stroke="#fff"/></svg>
    </li>
    <li>www.brightvanepower.example
      <svg viewBox="0 0 12 12"><circle cx="6" cy="6" r="5" fill="none" stroke="#fff"/><ellipse cx="6" cy="6" rx="2.2" ry="5" fill="none" stroke="#fff"/><path d="M1 6 H11" stroke="#fff"/></svg>
    </li>
  </ul>
</section>

</body>
</html>
```